Redesign current business card for food company

i would like to redesign my business card. our company is food company, our product range from chips, juices, milk and etc (mostly dried food stuff).
I want o keep same logo but , the rest is open to new design.
you can check at our website about our company www.orvelpantry.com

Target Market(s)

most of food company

Industry/Entity Type

Business

Contact Information for Business Card

I want to keep more to blue color...

Colors
3176b5
abd036

Requirements
Must have
• our old logo
Nice to have
• we do not mind to have nice material on bus card in order to accomplish nice design. for example: using spot uv, embossed and etc.

```html
<!DOCTYPE html>
<html lang="en">
<head>
<meta charset="utf-8">
<title>Orvel Pantry — Business Card</title>
<link rel="stylesheet" href="https://fonts.googleapis.com/css2?family=Source+Sans+3:wght@400;600;700&display=swap">
<style>
  :root {
    --backdrop: #161616;
    --card-white: #ffffff;
    --brand-blue: #1d6fb8;
    --brand-deep: #1657a0;
    --ink: #222222;
    --blue-top: #178fd0;
    --blue-bottom: #1a5a9e;
    --logo-light: #dbe9f5;
    --warm-soft: #fff3c4;
    --warm-peach: #fde1c6;
  }
  * { margin: 0; padding: 0; box-sizing: border-box; }
  html, body { width: 1200px; height: 900px; overflow: hidden; }
  body {
    position: relative;
    background: var(--backdrop);
    font-family: "Source Sans 3", "Myriad Pro", sans-serif;
  }
  .card {
    position: absolute;
    top: 170px;
    width: 347px;
    height: 561px;
    overflow: hidden;
  }
  .card--front { left: 259px; background: var(--card-white); }
  .card--back {
    left: 631px;
    background: linear-gradient(180deg, var(--blue-top) 0%, var(--blue-bottom) 100%);
  }
  .front-wash {
    position: absolute;
    left: 0; right: 0; bottom: 0;
    height: 320px;
    background: linear-gradient(160deg, rgba(255,255,255,0) 0%, var(--warm-soft) 45%, var(--warm-peach) 100%);
  }
  .back-wash {
    position: absolute;
    left: 0; right: 0; bottom: 0;
    height: 330px;
    background: linear-gradient(180deg, rgba(255,255,255,0) 0%, rgba(255,255,255,0.05) 100%);
  }
  .wordmark {
    position: absolute;
    left: 0; right: 0;
    text-align: center;
    font-weight: 700;
    font-size: 84px;
    line-height: 1;
    letter-spacing: -1px;
  }
  .card--front .wordmark { top: 82px; color: var(--brand-blue); }
  .card--back .wordmark { top: 238px; color: var(--logo-light); }
  .contact {
    position: absolute;
    left: 0; right: 0;
    top: 259px;
    text-align: center;
    color: var(--ink);
    font-size: 15px;
    line-height: 20px;
  }
  .contact__name { color: var(--brand-blue); font-weight: 600; font-size: 19px; line-height: 24px; }
  .contact__role { margin-bottom: 14px; }
  .contact__phones { margin-bottom: 13px; }
  .contact__web { margin-bottom: 13px; }
  .contact__company { color: var(--brand-deep); font-weight: 600; }
</style>
</head>
<body>
  <section class="card card--front">
    <div class="front-wash"></div>
    <div class="wordmark">orvel</div>
    <div class="contact">
      <p class="contact__name">Daniel Hartono</p>
      <p class="contact__role">President</p>
      <div class="contact__phones">
        <p>555 014 2288</p>
        <p>555 014 2277</p>
        <p>555 019 4410</p>
      </div>
      <p>Daniel@orvelpantry.com</p>
      <p class="contact__web">www.orvelpantry.com</p>
      <p class="contact__company">Orvel Enterprises Corp.</p>
      <p>1480 W 5th St.Fairmont CA 91700</p>
    </div>
  </section>
  <section class="card card--back">
    <div class="back-wash"></div>
    <div class="wordmark">orvel</div>
  </section>
</body>
</html>
```